Need Business Card for our Real Estate Business with Sales Executive's Picture

PANTONE 484 C ( RED)

PANTONE 2766 C ( BLUE

Industry/Entity Type

Real Estate

Contact Information for Business Card

Name, Mobile, email, & picture of Person
Agency Phone, address, Web address

Requirements
Must have
• Our Logo Colours, Agent Picture,

```html
<!DOCTYPE html>
<html lang="en">
<head>
<meta charset="utf-8">
<title>Mesa Ridge Realty – Business Card</title>
<link rel="stylesheet" href="https://fonts.googleapis.com/css2?family=Open+Sans:wght@400;600&family=Signika:wght@600&display=swap">
<style>
  :root {
    --navy: #1f2a5c;
    --red: #9b2a2a;
    --text: #1f2433;
    --card: #f3f1ee;
    --page: #dcdad6;
  }
  * { box-sizing: border-box; margin: 0; padding: 0; }
  html, body { width: 1200px; height: 1054px; overflow: hidden; }
  body {
    background: var(--page);
    font-family: "Open Sans", Arial, sans-serif;
    color: var(--text);
    position: relative;
  }
  .card {
    position: absolute;
    left: 100px; top: 224px;
    width: 1000px; height: 606px;
    background: var(--card);
    overflow: hidden;
    box-shadow: 0 10px 30px rgba(0,0,0,.15);
  }
  .brand {
    position: absolute;
    left: 58px; top: 160px;
    width: 332px;
    display: flex; align-items: center; justify-content: center; gap: 12px;
  }
  .brand-mark { width: 16px; height: 16px; background: var(--red); }
  .brand-name {
    font-size: 34px; font-weight: 600; color: var(--navy);
    letter-spacing: 1px; white-space: nowrap;
  }
  .agent-photo {
    position: absolute;
    left: 0; top: 312px;
    width: 306px; height: 294px;
    background: linear-gradient(180deg, #e7dfd8 0%, #c9a58c 45%, #283563 80%, #1f2a5c 100%);
  }
  .red-band {
    position: absolute;
    left: 306px; top: 579px;
    width: 180px; height: 27px;
    background: var(--red);
  }
  .navy-band {
    position: absolute;
    left: 462px; top: 528px;
    width: 538px; height: 78px;
    background: var(--navy);
    border-top-left-radius: 60px 78px;
  }
  .website {
    position: absolute;
    left: 536px; top: 551px;
    font-size: 23px; color: #e6e8f0;
  }
  .person-name {
    position: absolute; left: 536px; top: 222px;
    font-family: "Signika", "Open Sans", sans-serif;
    font-weight: 600; font-size: 34px; color: var(--navy);
  }
  .person-title {
    position: absolute; left: 536px; top: 266px;
    font-size: 24px; color: var(--red);
  }
  .address {
    position: absolute; left: 536px; top: 323px;
    font-size: 23px; line-height: 33px; color: var(--text);
  }
  .contacts {
    position: absolute; left: 540px; top: 407px;
    list-style: none;
  }
  .contacts li {
    display: flex; align-items: center; gap: 16px;
    height: 32.5px; font-size: 23px; color: var(--text);
  }
  .contacts svg { width: 20px; height: 20px; fill: var(--red); flex: none; }
</style>
</head>
<body>
  <section class="card">
    <div class="brand">
      <span class="brand-mark"></span>
      <span class="brand-name">Mesa Ridge Realty</span>
    </div>

    <div class="agent-photo" role="img" aria-label="Portrait photo of the sales executive"></div>

    <div class="red-band"></div>
    <div class="navy-band"></div>
    <div class="website">www.mesaridgerealty.com</div>

    <h1 class="person-name">Laura Whitfield</h1>
    <p class="person-title">Managing Director</p>
    <p class="address">418 Cedar Park Ave #2210,<br>Fairview, CO 80511</p>

    <ul class="contacts">
      <li>
        <svg viewBox="0 0 20 20" aria-hidden="true"><path d="M6 1h8a2 2 0 0 1 2 2v14a2 2 0 0 1-2 2H6a2 2 0 0 1-2-2V3a2 2 0 0 1 2-2zm0 3v10h8V4zm4 11.5a1.2 1.2 0 1 0 0 2.4 1.2 1.2 0 0 0 0-2.4z"/></svg>
        <span>555.201.3344</span>
      </li>
      <li>
        <svg viewBox="0 0 20 20" aria-hidden="true"><path d="M2 6c0-2 3-3.5 8-3.5S18 4 18 6v2h-4V6.5c-1-.4-2.5-.6-4-.6s-3 .2-4 .6V8H2zm3 3h10l2 8H3zm5 2a2.5 2.5 0 1 0 0 5 2.5 2.5 0 0 0 0-5z"/></svg>
        <span>555-301-7788</span>
      </li>
      <li>
        <svg viewBox="0 0 20 20" aria-hidden="true"><path d="M1 4h18v12H1zm2 2v.4l7 4.6 7-4.6V6l-7 4.5z"/></svg>
        <span>lwhitfield@mesaridgerealty.com</span>
      </li>
    </ul>
  </section>
</body>
</html>
```